New start-up company catalog!

Heat transfer printing company. We are set to launch later this month and need a stand out catalog to wow our customers. We are a printing/manufacturing heat transfer company geared towards apparel and promotional items.

```html
<!DOCTYPE html>
<html lang="en">
<head>
<meta charset="utf-8">
<title>Classic Formula Heat Transfers – Catalog Spread</title>
<link href="https://fonts.googleapis.com/css2?family=Bungee&family=Montserrat:wght@500;600;700;800&family=Open+Sans:wght@600;700&family=Roboto+Condensed:wght@400;700&display=swap" rel="stylesheet">
<style>
:root{
  --backdrop:#6d6e71;
  --paper:#ffffff;
  --purple:#3b2a86;
  --purple-deep:#2e1f6e;
  --violet:#6a3fa0;
  --orange:#f5a623;
  --orange-deep:#f08c1a;
  --teal:#3fc1c0;
  --teal-light:#d5f1f1;
  --magenta:#e6007e;
  --ink:#231f20;
  --grey:#bcbec0;
}
*{box-sizing:border-box;margin:0;padding:0}
html,body{width:1200px;height:493px;overflow:hidden;background:var(--backdrop)}
.spread{position:relative;width:1200px;height:493px}
.page{position:absolute;top:40px;width:536px;height:416px;background:var(--paper);overflow:hidden}
.page--left{left:60px}
.page--right{left:602px}
.folio{position:absolute;bottom:0;width:9px;height:9px;background:var(--magenta)}
.page--left .folio{left:0}
.page--right .folio{right:0}

/* left page */
.hero-photo{position:absolute;left:0;top:0;width:536px;height:256px;
  background:linear-gradient(160deg,var(--teal) 0%,#39b3b4 45%,#1f3b3a 75%,#8a1c2c 100%)}
.title{position:absolute;left:366px;top:14px;font-family:'Bungee',sans-serif;font-size:21px;line-height:20px}
.title span{display:block;width:max-content;background:var(--purple);color:var(--orange);padding:0 3px;margin-left:auto}
.title .t1{margin-left:4px}
.title .t3{margin-right:16px}
.title .t4{color:var(--teal)}
.blend-band{position:absolute;left:12px;top:238px;width:524px;height:84px;
  background:linear-gradient(90deg,var(--purple-deep),var(--violet))}
.blend-band h2{position:absolute;left:10px;top:8px;font-family:'Montserrat',sans-serif;font-weight:700;
  color:#fff;font-size:21px;line-height:24px;letter-spacing:.5px}
.blend-band p{position:absolute;left:282px;top:8px;width:236px;font-family:'Open Sans',sans-serif;
  font-weight:600;font-size:8.2px;line-height:10.4px;color:var(--orange)}
.color-tag{position:absolute;left:424px;top:316px;width:112px;height:18px;background:var(--teal);
  color:#fff;font-family:'Montserrat',sans-serif;font-weight:700;font-size:11px;line-height:18px;text-align:center}

.scale{position:absolute;left:27px;width:140px;font-family:'Montserrat',sans-serif}
.scale h3{text-align:center;color:var(--purple);font-size:10px;font-weight:700}
.scale .bar{position:relative;height:6px;margin-top:3px;
  background:linear-gradient(90deg,var(--orange) 88%,transparent 88%),repeating-linear-gradient(90deg,var(--grey) 0 2px,transparent 2px 4px)}
.scale .marker{position:absolute;top:-5px;width:0;height:0;border-left:3px solid transparent;border-right:3px solid transparent;border-top:4px solid var(--teal)}
.scale .ends{display:flex;justify-content:space-between;font-size:7px;color:var(--ink);margin-top:2px;font-weight:600}
.scale--feel{top:332px}
.scale--opacity{top:367px}

.stat{position:absolute;top:342px;width:64px;text-align:center;font-family:'Montserrat',sans-serif}
.stat .box{position:relative;height:46px;border:4px solid var(--orange);box-shadow:4px 4px 0 var(--grey);background:#fff}
.stat .num{display:block;color:var(--teal);font-weight:800;font-size:22px;line-height:24px;margin-top:2px}
.stat .unit{display:block;color:var(--teal);font-weight:700;font-size:8px}
.stat .label{display:block;color:var(--purple);font-weight:700;font-size:10px;margin-top:6px}
.stat--time{left:208px}
.stat--temp{left:292px}
.stat--psi{left:372px}
.stat--peel{left:456px}
.stat--peel svg{margin-top:6px}

/* right page */
.section-bar{position:absolute;left:18px;width:506px;background:linear-gradient(90deg,var(--purple-deep),var(--violet));
  color:#fff;font-family:'Montserrat',sans-serif;font-weight:700}
.section-bar--main{top:10px;height:22px;font-size:15px;line-height:22px;padding-left:8px}
.section-bar--sub{height:21px;font-size:7.5px;line-height:8px;padding:3px 8px}
.section-bar--essential{top:210px}
.section-bar--stretch{top:331px}

.art-sample{position:absolute;left:48px;top:90px;width:102px;height:86px;border:1px dashed var(--grey);
  background:linear-gradient(135deg,#eef0f8,#dfe3f2)}
.dim{position:absolute;font-family:'Open Sans',sans-serif;font-size:7px;color:var(--ink)}
.dim--w{left:48px;top:72px;width:102px;text-align:center}
.dim--h{left:36px;top:128px}
.dim-line{position:absolute;background:var(--ink)}

.price{position:absolute;width:118px;border-collapse:collapse;font-family:'Roboto Condensed',sans-serif;font-size:5.4px;line-height:6.6px;color:var(--ink)}
.price th{background:var(--purple);color:#fff;font-weight:700;text-align:left;padding:0 2px}
.price td{padding:0 2px;text-align:left}
.price td:first-child{text-align:right;padding-right:5px;font-weight:700}
.price tr:nth-child(even) td{background:var(--teal-light)}
.price--a{left:200px;top:42px}
.price--b{left:324px;top:42px;width:120px}
.price--c{left:200px;top:124px}
.price--d{left:324px;top:124px;width:120px}

.no-gang{position:absolute;left:466px;top:150px;width:56px;text-align:center;font-family:'Open Sans',sans-serif;font-size:4.5px;font-weight:700}

.swatches{position:absolute;left:18px;display:grid;grid-template-columns:repeat(11,40px);column-gap:5.4px;row-gap:6px}
.swatches--essential{top:238px}
.swatches--stretch{top:358px}
.swatch{position:relative;height:40px;background:var(--c);border:1px solid rgba(0,0,0,.08)}
.swatch span{position:absolute;left:2px;bottom:2px;font-family:'Open Sans',sans-serif;font-weight:700;font-size:5.6px;line-height:6.2px;color:#fff}
.swatch.light span{color:var(--ink)}
.swatch.white{border:1px solid #999}
</style>
</head>
<body>
<div class="spread">

  <section class="page page--left">
    <div class="hero-photo" role="img" aria-label="Photo of four printed t-shirts in maroon, black, red and green on a teal backdrop"></div>
    <h1 class="title"><span class="t1">CLASSIC</span><span class="t2">FORMULA</span><span class="t3">HEAT</span><span class="t4">TRANSFERS</span></h1>

    <div class="blend-band">
      <h2>FOR COTTON<br>AND<br>COTTON/POLY BLENDS</h2>
      <p>Our Classic ink formula is designed to print on 100% cotton &amp; 50/50 cotton-poly blends. The ink has a very soft feel. Add a distress pattern to your design and give your logo a “classic” time-worn look. Gang sheets allow you to print multiple logos for the same low price! Application is quick and easy! Hot peel them in only 7 seconds!</p>
    </div>
    <div class="color-tag">1, 2, 3 Color</div>

    <div class="scale scale--feel">
      <h3>Feel</h3>
      <div class="bar"><i class="marker" style="left:120px"></i></div>
      <div class="ends"><span>Soft</span><span>Heavy</span></div>
    </div>
    <div class="scale scale--opacity">
      <h3>Opacity</h3>
      <div class="bar"><i class="marker" style="left:120px"></i></div>
      <div class="ends"><span>Transparent</span><span>Opaque</span></div>
    </div>

    <div class="stat stat--time"><div class="box"><span class="num">7</span><span class="unit">Seconds</span></div><span class="label">Time</span></div>
    <div class="stat stat--temp"><div class="box"><span class="num">325</span><span class="unit">Degrees</span></div><span class="label">Temprature</span></div>
    <div class="stat stat--psi"><div class="box"><span class="num">60</span><span class="unit">PSI</span></div><span class="label">Pressure</span></div>
    <div class="stat stat--peel"><div class="box">
      <svg width="24" height="30" viewBox="0 0 24 30" fill="none" stroke="#f08c1a" stroke-width="2.4" stroke-linecap="round">
        <path d="M5 28c-4-6 4-9 0-15s3-9 1-12"/><path d="M12 28c-4-6 4-9 0-15s3-9 1-12"/><path d="M19 28c-4-6 4-9 0-15s3-9 1-12"/>
      </svg></div><span class="label">Hot Peel</span></div>

    <i class="folio"></i>
  </section>

  <section class="page page--right">
    <h2 class="section-bar section-bar--main">Sizing &amp; Pricing</h2>

    <span class="dim dim--w">12.75"</span>
    <i class="dim-line" style="left:48px;top:82px;width:102px;height:1px"></i>
    <span class="dim dim--h">9"</span>
    <i class="dim-line" style="left:43px;top:90px;width:1px;height:86px"></i>
    <div class="art-sample" role="img" aria-label="Sample hand-lettered slogan artwork in navy blue"></div>

    <table class="price price--a">
      <tr><th>Classic 4x6</th><th>1 color</th><th>2 color</th><th>3 color</th></tr>
      <tr><td>8</td><td>$ 4.83</td><td>$ 8.88</td><td>$12.58</td></tr>
      <tr><td>16</td><td>$ 2.43</td><td>$ 4.58</td><td>$ 6.38</td></tr>
      <tr><td>24</td><td>$ 1.63</td><td>$ 3.08</td><td>$ 4.28</td></tr>
      <tr><td>32</td><td>$ 1.28</td><td>$ 2.48</td><td>$ 3.28</td></tr>
      <tr><td>48</td><td>$ 1.13</td><td>$ 2.08</td><td>$ 3.03</td></tr>
      <tr><td>72</td><td>$ 0.88</td><td>$ 1.53</td><td>$ 2.38</td></tr>
      <tr><td>96</td><td>$ 0.68</td><td>$ 1.18</td><td>$ 1.78</td></tr>
      <tr><td>144</td><td>$ 0.48</td><td>$ 1.13</td><td>$ 1.23</td></tr>
      <tr><td>288</td><td>$ 0.38</td><td>$ 0.58</td><td>$ 0.88</td></tr>
      <tr><td>512</td><td>$ 0.23</td><td>$ 0.48</td><td>$ 0.63</td></tr>
    </table>
    <table class="price price--b">
      <tr><th>Classic 6x9</th><th>1 color</th><th>2 color</th><th>3 color</th></tr>
      <tr><td>8</td><td>$ 6.28</td><td>$ 11.73</td><td>$ 17.28</td></tr>
      <tr><td>16</td><td>$ 3.18</td><td>$ 5.98</td><td>$ 8.63</td></tr>
      <tr><td>24</td><td>$ 2.18</td><td>$ 4.03</td><td>$ 5.78</td></tr>
      <tr><td>32</td><td>$ 1.73</td><td>$ 3.13</td><td>$ 4.48</td></tr>
      <tr><td>48</td><td>$ 1.53</td><td>$ 2.68</td><td>$ 3.93</td></tr>
      <tr><td>72</td><td>$ 1.28</td><td>$ 2.23</td><td>$ 3.18</td></tr>
      <tr><td>96</td><td>$ 1.08</td><td>$ 1.88</td><td>$ 2.68</td></tr>
      <tr><td>144</td><td>$ 0.98</td><td>$ 1.52</td><td>$ 2.18</td></tr>
      <tr><td>288</td><td>$ 0.68</td><td>$ 1.06</td><td>$ 2.53</td></tr>
      <tr><td>512</td><td>$ 0.48</td><td>$ 0.83</td><td>$ 1.23</td></tr>
    </table>
    <table class="price price--c">
      <tr><th>Classic 9x12.75</th><th>1 color</th><th>2 color</th><th>3 color</th></tr>
      <tr><td>8</td><td>$ 6.98</td><td>$13.13</td><td>$19.13</td></tr>
      <tr><td>16</td><td>$ 3.68</td><td>$ 6.68</td><td>$ 9.58</td></tr>
      <tr><td>24</td><td>$ 2.48</td><td>$ 4.48</td><td>$ 6.43</td></tr>
      <tr><td>32</td><td>$ 2.18</td><td>$ 3.63</td><td>$ 5.13</td></tr>
      <tr><td>48</td><td>$ 1.78</td><td>$ 3.08</td><td>$ 4.33</td></tr>
      <tr><td>72</td><td>$ 1.53</td><td>$ 2.48</td><td>$ 3.58</td></tr>
      <tr><td>96</td><td>$ 1.28</td><td>$ 2.18</td><td>$ 3.13</td></tr>
      <tr><td>144</td><td>$ 1.13</td><td>$ 1.98</td><td>$ 2.58</td></tr>
      <tr><td>288</td><td>$ 0.83</td><td>$ 1.38</td><td>$ 1.88</td></tr>
      <tr><td>512</td><td>$ 0.58</td><td>$ 1.03</td><td>$ 1.48</td></tr>
    </table>
    <table class="price price--d">
      <tr><th>Classic 12x12.75</th><th>1 color</th><th>2 color</th><th>3 color</th></tr>
      <tr><td>8</td><td>$ 8.33</td><td>$ 16.13</td><td>$23.98</td></tr>
      <tr><td>16</td><td>$ 4.93</td><td>$ 8.93</td><td>$13.03</td></tr>
      <tr><td>24</td><td>$ 3.43</td><td>$ 5.98</td><td>$ 8.73</td></tr>
      <tr><td>32</td><td>$ 2.88</td><td>$ 5.13</td><td>$ 7.33</td></tr>
      <tr><td>48</td><td>$ 2.18</td><td>$ 3.73</td><td>$ 5.38</td></tr>
      <tr><td>72</td><td>$ 1.78</td><td>$ 3.23</td><td>$ 4.83</td></tr>
      <tr><td>96</td><td>$ 1.53</td><td>$ 2.58</td><td>$ 3.93</td></tr>
      <tr><td>144</td><td>$ 1.28</td><td>$ 2.48</td><td>$ 3.03</td></tr>
      <tr><td>288</td><td>$ 0.98</td><td>$ 1.63</td><td>$ 2.23</td></tr>
      <tr><td>512</td><td>$ 0.68</td><td>$ 1.13</td><td>$ 1.73</td></tr>
    </table>

    <div class="no-gang">
      No Art Ganging
      <svg width="44" height="44" viewBox="0 0 44 44">
        <rect x="12" y="12" width="20" height="20" fill="none" stroke="#999" stroke-width="1"/>
        <rect x="14" y="14" width="7" height="6" fill="#3aa64a"/><rect x="23" y="14" width="7" height="6" fill="#3aa64a"/>
        <rect x="14" y="23" width="7" height="6" fill="#3aa64a"/><rect x="23" y="23" width="7" height="6" fill="#3aa64a"/>
        <circle cx="22" cy="22" r="19" fill="none" stroke="#e02020" stroke-width="2"/>
        <line x1="8.6" y1="8.6" x2="35.4" y2="35.4" stroke="#e02020" stroke-width="2"/>
      </svg>
    </div>

    <h3 class="section-bar section-bar--sub section-bar--essential">Available Colors:<br>Essential, Nylon</h3>
    <div class="swatches swatches--essential">
      <div class="swatch" style="--c:#000"><span>Black</span></div>
      <div class="swatch" style="--c:#9ea2a6"><span>Gray<br>7543C</span></div>
      <div class="swatch" style="--c:#8a1f3c"><span>Burgundy<br>194C</span></div>
      <div class="swatch" style="--c:#b41f2e"><span>Red<br>187C</span></div>
      <div class="swatch" style="--c:#d0197e"><span>Hot Pink<br>232c</span></div>
      <div class="swatch" style="--c:#f19cbd"><span>Pink<br>1905C</span></div>
      <div class="swatch" style="--c:#3a2766"><span>Purple<br>2685C</span></div>
      <div class="swatch" style="--c:#1b3565"><span>Navy<br>654C</span></div>
      <div class="swatch" style="--c:#203e8a"><span>Royal<br>287C</span></div>
      <div class="swatch" style="--c:#28a0d8"><span>Columbia<br>299C</span></div>
      <div class="swatch" style="--c:#13b4e4"><span>Bright Blue<br>306C</span></div>
      <div class="swatch" style="--c:#50362a"><span>Brown<br>476C</span></div>
      <div class="swatch" style="--c:#17302a"><span>Dark Green<br>5535C</span></div>
      <div class="swatch" style="--c:#1a8a3e"><span>Kelly Green<br>348C</span></div>
      <div class="swatch" style="--c:#8bc43f"><span>Bright<br>Green<br>375C</span></div>
      <div class="swatch" style="--c:#a08c43"><span>Vegas<br>Gold<br>4505C</span></div>
      <div class="swatch" style="--c:#c6541f"><span>Texas<br>Orange<br>1525C</span></div>
      <div class="swatch" style="--c:#ef5a24"><span>Bright<br>Orange<br>021C</span></div>
      <div class="swatch" style="--c:#f15a29"><span>Orange<br>172C</span></div>
      <div class="swatch" style="--c:#fbb034"><span>Gold<br>1235C</span></div>
      <div class="swatch light" style="--c:#ffe600"><span>Yellow<br>YellowC</span></div>
      <div class="swatch light white" style="--c:#fff"><span>White</span></div>
    </div>

    <h3 class="section-bar section-bar--sub section-bar--stretch">Available Colors:<br>Stretch</h3>
    <div class="swatches swatches--stretch">
      <div class="swatch" style="--c:#000"><span>Black</span></div>
      <div class="swatch" style="--c:#9ea2a6"><span>Gray<br>7543C</span></div>
      <div class="swatch" style="--c:#b41f2e"><span>Red<br>187C</span></div>
      <div class="swatch" style="--c:#f19cbd"><span>Pink<br>1905C</span></div>
      <div class="swatch" style="--c:#1b3565"><span>Navy<br>654C</span></div>
      <div class="swatch" style="--c:#203e8a"><span>Royal<br>287C</span></div>
      <div class="swatch" style="--c:#fbb034"><span>Gold<br>1235C</span></div>
      <div class="swatch light" style="--c:#ffe600"><span>Yellow<br>YellowC</span></div>
      <div class="swatch light white" style="--c:#fff"><span>White</span></div>
    </div>

    <i class="folio"></i>
  </section>

</div>
</body>
</html>
```